Where the Lantern Fades: A Sacred Wandering

This is a memoir about my breakdown/breakthrough followed by a spiritual awakening in 2012, I found my guru Harsh Omveli Dev, Mother Ayahuasca, and my spiritual mother, Ishu. By 2013, I was headed for a spiritual adventure through India, Southeast India, and Nepal which lasted 14 months. I lived in ashrams, meditated and prayed in temples,, traveled by train and bus, met many enlightened beings and interesting people. During Vipassana, I discovered my true essence- the light of my soul. It is a book of travel, romance, and spiritual growth. My idea is a road lined with temples, etc. I am walking down the road and see myself at the end of the road, facing out, with a bright star in my heart center. I see the colors in muted yellows and other earth-tone hues. Marigolds are used everywhere in the temples to adorn statues and doorways and this speaks to me. The title of the book is about finding out who I am beyond my stories and it is also about how our story will reveal to us who we really are.

Target Market(s)

Spiritual seekers, adventurers, travelers

Industry/Entity Type

Spiritual

Font styles to use
Serif
Sans Serif
Other font styles liked:
• I’m open. I like simplicity

Colors
FFC000
F8CF3A
FAE287
FDF2CF
FEFAEE

Requirements
Must have
• My name: Carla Serena Tovi, Earth tones, pastels, me or a likeness of me, room for ISBN on back cover
Nice to have
• In the photo uploads I drew an idea of what I would like, there is also the idea in the book
Should not have
• I am not a fan of bright colors and that's all I can select here. I like neutral colors, like browns, slate, creams, and whites. This reflects the dusty roads I took throughout my journey.

```html
<!DOCTYPE html>
<html lang="en">
<head>
<meta charset="UTF-8">
<title>Where the Lantern Fades — Book Cover</title>
<link rel="stylesheet" href="https://fonts.googleapis.com/css2?family=Cinzel:wght@400;500&family=Cormorant+Garamond:ital,wght@1,500&display=swap">
<style>
  :root {
    --backdrop: #282828;
    --paper: #ffffff;
    --marigold: #f4a90c;
    --ink: #000000;
    --dust: #d8d0c2;
  }
  * { margin: 0; padding: 0; box-sizing: border-box; }
  html, body {
    width: 1200px;
    height: 1200px;
    overflow: hidden;
    background: var(--backdrop);
  }
  .canvas {
    position: relative;
    width: 1200px;
    height: 1200px;
  }
  .cover {
    position: absolute;
    left: 219px;
    top: 26px;
    width: 770px;
    height: 1138px;
    background: var(--paper);
  }
  .title-word {
    position: absolute;
    left: 0;
    width: 100%;
    text-align: center;
    font-family: "Cinzel", "Trajan Pro", serif;
    font-weight: 400;
    font-size: 138px;
    line-height: 1;
    letter-spacing: 0.06em;
    color: var(--marigold);
  }
  .title-word--key {
    color: var(--ink);
    font-size: 122px;
    letter-spacing: 0.04em;
  }
  .w-where   { top: 90px; }
  .w-the     { top: 290px; }
  .w-lantern { top: 498px; }
  .w-fades   { top: 706px; }
  .subtitle {
    position: absolute;
    right: 110px;
    top: 868px;
    font-family: "Cormorant Garamond", "Garamond", serif;
    font-style: italic;
    font-weight: 500;
    font-size: 46px;
    letter-spacing: 0.2em;
    color: var(--ink);
    line-height: 1;
  }
  .figure {
    position: absolute;
    left: 672px;
    top: 620px;
    width: 62px;
    height: 240px;
    border-radius: 30px 30px 12px 12px;
    background: var(--dust);
  }
  .author {
    position: absolute;
    left: 0;
    width: 100%;
    top: 1062px;
    text-align: center;
    font-family: "Cinzel", "Trajan Pro", serif;
    font-weight: 400;
    font-size: 29px;
    letter-spacing: 0.1em;
    color: var(--ink);
    line-height: 1;
  }
</style>
</head>
<body>
  <div class="canvas">
    <div class="cover">
      <h1 class="title">
        <span class="title-word w-where">WHERE</span>
        <span class="title-word w-the">THE</span>
        <span class="title-word title-word--key w-lantern">LANTERN</span>
        <span class="title-word w-fades">FADES</span>
      </h1>
      <div class="figure" role="img" aria-label="Soft beige silhouette of a woman in a dress, walking"></div>
      <p class="subtitle">A Sacred Wandering</p>
      <p class="author">CARLA SERENA TOVI</p>
    </div>
  </div>
</body>
</html>
```